Best local air conditioning and heating contractor

We need a website design for a new company in Tampa Bay called the Coastal Breeze Cooling Company. We provide superior services for residential and commercial properties as well as maintenance and installing HVAC systems. We also want to sell equipment, parts and filter on the website as well. We want it easy to use for customers. Rich with content and keywords for our area.

Target Market(s)

homeowners in Tampa Bay

Industry/Entity Type

HVAC air conditioning and heating

Coding

Coded - Design and coding required

Number of Pages Required

5+ page

Font styles to use
Sans Serif

Requirements
Nice to have
• would like the colors to be same as logo

```html
<!DOCTYPE html>
<html lang="en">
<head>
<meta charset="utf-8">
<title>Coastal Breeze Cooling Company</title>
<link href="https://fonts.googleapis.com/css2?family=Oswald:wght@500;700&family=Roboto:wght@400;500;700&display=swap" rel="stylesheet">
<style>
:root{--navy:#1f2d6b;--navy-dark:#1a265c;--red:#d71f26;--ink:#222;--muted:#555;--white:#fff;--line:#cfcfcf}
*{box-sizing:border-box;margin:0;padding:0}
html,body{width:1200px;height:4874px;overflow:hidden}
body{position:relative;font-family:'Roboto',Arial,sans-serif;color:var(--ink);background:var(--white)}
.abs{position:absolute}
.head{font-family:'Oswald',Impact,sans-serif;font-weight:700;text-transform:uppercase;letter-spacing:.5px}
.photo{position:absolute}
/* header */
.site-header{position:absolute;left:0;top:0;width:1200px;height:85px;background:var(--white)}
.brand{position:absolute;display:flex;align-items:center;gap:8px;font-family:'Oswald',sans-serif;font-weight:700;color:var(--navy);font-size:15px;line-height:1.05;text-transform:uppercase}
.brand .dot{width:18px;height:18px;border-radius:50%;background:var(--red);flex:none}
.nav a{position:absolute;top:35px;font-size:13px;color:#333;text-decoration:none}
.nav a.active{color:var(--red)}
.nav a.active::before{content:"";position:absolute;left:-4px;right:-4px;top:-8px;height:2px;background:var(--red)}
.call{position:absolute;left:875px;top:22px;width:40px;height:40px;border-radius:50%;background:var(--red);display:flex;align-items:center;justify-content:center}
.call-text{position:absolute;left:926px;top:20px;font-size:12px;color:#333}
.call-text b{display:block;font-size:20px;color:var(--navy);font-weight:700;margin-top:2px}
/* hero */
.hero{left:0;top:85px;width:1200px;height:687px;background:linear-gradient(90deg,#d9d6d2 0%,#ecebea 35%,#f1f0ef 60%,#e6dcd6 85%,#d8cdc7 100%)}
.hero-title{position:absolute;left:0;width:1200px;top:360px;text-align:center;color:var(--navy);font-size:62px;line-height:70px}
.btn-skew{position:absolute;background:var(--red);color:#fff;font-family:'Oswald',sans-serif;font-weight:500;font-size:13px;text-transform:uppercase;display:flex;align-items:center;justify-content:center;clip-path:polygon(0 0,100% 0,86% 100%,0 100%)}
.round{position:absolute;border-radius:50%;display:flex;align-items:center;justify-content:center}
/* services */
.services{left:0;top:772px;width:1200px;height:750px}
.section-title{position:absolute;left:0;width:1200px;text-align:center;font-size:46px}
.svc-card{position:absolute;top:939px;width:303px;height:375px}
.svc-card .photo{left:0;top:0;width:303px;height:229px}
.svc-body{position:absolute;left:0;top:197px;width:278px;height:178px;background:#fff;border-top:4px solid var(--red);padding:22px 20px 0}
.svc-body h3{font-size:17px;color:#222;margin-bottom:8px}
.svc-body p{font-size:11px;line-height:19px;color:#555}
.svc-body .more{position:absolute;right:0;bottom:0;width:114px;height:27px;font-size:11px;clip-path:polygon(14% 0,100% 0,100% 100%,0 100%)}
/* about */
.about-text{position:absolute;left:626px;top:1668px;width:462px;font-size:13px;line-height:21px;color:#555;text-align:justify}
.feature{position:absolute;top:2042px;width:220px;height:148px;background:#fff;box-shadow:0 4px 14px rgba(0,0,0,.12);text-align:center;padding-top:22px}
.feature p{font-size:11px;font-weight:700;line-height:18px;color:#222;margin-top:10px}
/* products */
.product{position:absolute;top:2389px;width:381px;height:475px}
.product .frame{position:absolute;left:27px;top:28px;width:327px;height:340px;background:#fff;border-radius:6px}
.product h3{position:absolute;left:0;width:100%;top:404px;text-align:center;color:#fff;font-family:'Oswald',sans-serif;font-weight:500;font-size:22px}
/* portfolio */
.portfolio{left:0;top:2970px;width:1200px;height:810px;background:var(--red)}
/* contact */
.field{position:absolute;border:1px solid var(--line);border-radius:3px;font-size:13px;color:#666;padding:0 20px;display:flex;align-items:center}
/* footer */
.footer{left:0;top:4378px;width:1200px;height:496px}
.foot-h{position:absolute;top:4522px;font-size:21px;font-weight:700;color:#fff}
.foot-h::after{content:"";position:absolute;left:0;top:40px;width:36px;height:2px;background:#fff}
.foot-list{position:absolute;top:4580px;list-style:none;font-size:14px;line-height:22px;color:#fff}
.contact-item{position:absolute;left:833px;display:flex;align-items:center;gap:16px;font-size:14px;color:#fff}
.contact-item .ic{width:30px;height:30px;border-radius:50%;background:#fff;display:flex;align-items:center;justify-content:center}
.bottom-bar{position:absolute;left:0;top:4742px;width:1200px;height:132px;background:var(--navy-dark)}
.social{position:absolute;top:4806px;width:34px;height:34px;border-radius:50%;border:2px solid #fff}
</style>
</head>
<body>

<header class="site-header">
  <div class="brand" style="left:110px;top:22px;width:190px"><span class="dot"></span><span>Coastal Breeze<br>Cooling Company</span></div>
  <nav class="nav">
    <a class="active" style="left:423px">Home</a>
    <a style="left:502px">About us</a>
    <a style="left:598px">Services</a>
    <a style="left:693px">Blog</a>
    <a style="left:762px">Contact</a>
  </nav>
  <div class="call"><svg width="18" height="18" viewBox="0 0 24 24"><path fill="#fff" d="M6.6 10.8a15 15 0 0 0 6.6 6.6l2.2-2.2c.3-.3.7-.4 1-.2 1.1.4 2.3.6 3.6.6.6 0 1 .4 1 1V20c0 .6-.4 1-1 1A17 17 0 0 1 3 4c0-.6.4-1 1-1h3.5c.6 0 1 .4 1 1 0 1.3.2 2.5.6 3.6.1.3 0 .7-.2 1z"/></svg></div>
  <div class="call-text">Call us Today!<b>+1 555 014 2030</b></div>
</header>

<section class="photo hero" role="img" aria-label="HVAC technician and smiling homeowner with remote beside a wall-mounted air conditioner"></section>
<h1 class="head hero-title">Coastal Breeze<br>Cooling</h1>
<a class="btn-skew" style="left:502px;top:515px;width:125px;height:45px">Get Started</a>
<span class="round" style="left:527px;top:677px;width:36px;height:36px;background:#fff"><svg width="12" height="12" viewBox="0 0 12 12"><path d="M8 1 3 6l5 5" fill="none" stroke="#222" stroke-width="1.6"/></svg></span>
<span class="round" style="left:569px;top:677px;width:36px;height:36px;background:#fff"><svg width="12" height="12" viewBox="0 0 12 12"><path d="m4 1 5 5-5 5" fill="none" stroke="#222" stroke-width="1.6"/></svg></span>

<svg class="abs services" width="1200" height="750" viewBox="0 0 1200 750"><polygon points="0,0 1200,0 1200,748 600,660 0,748" fill="#1f2d6b"/><polygon points="0,748 600,660 1200,748 1200,742 600,662 0,742" fill="#d71f26"/><polygon points="0,748 0,732 600,662 1200,732 1200,748 600,668" fill="#d71f26"/></svg>
<h2 class="head section-title" style="top:853px;color:#fff">Superior Services</h2>
<span class="round" style="left:37px;top:1115px;width:40px;height:40px;border:2px solid #fff"><svg width="12" height="12" viewBox="0 0 12 12"><path d="M8 1 3 6l5 5" fill="none" stroke="#fff" stroke-width="1.6"/></svg></span>
<span class="round" style="left:1123px;top:1115px;width:40px;height:40px;border:2px solid #fff"><svg width="12" height="12" viewBox="0 0 12 12"><path d="m4 1 5 5-5 5" fill="none" stroke="#fff" stroke-width="1.6"/></svg></span>

<article class="svc-card" style="left:112px">
  <div class="photo" role="img" aria-label="Technician servicing an indoor split air conditioner in a home" style="background:linear-gradient(135deg,#e9e9e9,#c9d3e3 60%,#3a5fa8)"></div>
  <div class="svc-body"><h3 class="head">Residential</h3><p>Lorem ipsum dolor sit amet, consectetur ad ipiscing elit, sed do eiusmod tempor inci di dunt ut labore et dolore magna loremipsum dolor sit amet, consectetur</p><a class="btn-skew more">Learn More</a></div>
</article>
<article class="svc-card" style="left:449px">
  <div class="photo" role="img" aria-label="Worker inspecting rooftop commercial condenser units" style="background:linear-gradient(135deg,#f1f1f1,#cfcfcf 55%,#8c8a80)"></div>
  <div class="svc-body"><h3 class="head">Commercial Properties</h3><p>Lorem ipsum dolor sit amet, consectetur ad ipiscing elit, sed do eiusmod tempor inci di dunt ut labore et dolore magna loremipsum dolor sit amet, consectetur</p><a class="btn-skew more">Learn More</a></div>
</article>
<article class="svc-card" style="left:786px">
  <div class="photo" role="img" aria-label="Technician with gauges maintaining an outdoor HVAC unit" style="background:linear-gradient(135deg,#9fb0c4,#3d4f6e 55%,#b88a4a)"></div>
  <div class="svc-body"><h3 class="head">Maintenance and Installing</h3><p>Lorem ipsum dolor sit amet, consectetur ad ipiscing elit, sed do eiusmod tempor inci di dunt ut labore et dolore magna loremipsum dolor sit amet, consectetur</p><a class="btn-skew more">Learn More</a></div>
</article>

<div class="photo" role="img" aria-label="Technician in blue cap adjusting a wall air conditioner" style="left:112px;top:1609px;width:469px;height:511px;background:linear-gradient(135deg,#e4e4e4,#c8cbd0 45%,#2f5fb0 70%,#3b3d42)"></div>
<h2 class="head abs" style="left:626px;top:1596px;font-size:44px;color:#222">About Us</h2>
<div class="about-text">
  <p>Lorem ipsum dolor sit amet, consectetur adipiscing elit, sed do eius mod tempor incididunt ut labore et dolore magna aliqua. Ut enim ad minim veniam, quis nostrud exercitation ullamco laboris nisi ut aliquip ex ea commodo consequat. Duis aute irure dolor in reprehenderit in voluptate velit esse cillum dolore eu fugiat nulla pariatur.</p>
  <p style="margin-top:21px">Excepteur sint occaecat cupidatat non proident, sunt in culpa qui officia deserunt mollit anim id est laborum. Lorem ipsum dolor sit amet, consectetur adipiscing elit, sed do eiusmod tempor incididunt ut labore et dolore magna aliqua. Ut enim ad minim veniam, quis nostrud exercitation ullamco laboris nisi ut aliquip ex ea commodo consequat. Duis aute irure dolor in reprehenderit in voluptate velit esse cillum dolore eu fugiat nulla pariatur. Excepteur sint occaecat cupidatat non proident, sunt in culpa qui officia deserunt mollit anim id est laborum.</p>
</div>
<a class="btn-skew" style="left:626px;top:1982px;width:127px;height:33px;font-size:12px">Learn More</a>

<div class="feature" style="left:398px"><svg width="56" height="54" viewBox="0 0 56 54"><rect x="10" y="22" width="36" height="28" rx="2" fill="#d71f26"/><rect x="21" y="16" width="14" height="8" fill="none" stroke="#d71f26" stroke-width="3"/><rect x="10" y="34" width="36" height="3" fill="#fff"/><path d="M28 2l2 4 4 .5-3 3 .8 4-3.8-2-3.8 2 .8-4-3-3 4-.5z M10 6l1.5 3 3 .4-2.2 2 .6 3-2.9-1.5-2.9 1.5.6-3-2.2-2 3-.4z M46 6l1.5 3 3 .4-2.2 2 .6 3-2.9-1.5-2.9 1.5.6-3-2.2-2 3-.4z" fill="#d71f26"/></svg><p>25 YEARS IN<br>EXPERIENCES</p></div>
<div class="feature" style="left:634px"><svg width="56" height="54" viewBox="0 0 56 54"><path d="M28 4 4 26h7v24h34V26h7z" fill="#d71f26"/><circle cx="28" cy="33" r="8" fill="#fff"/><rect x="26" y="22" width="4" height="22" fill="#d71f26"/></svg><p>HIGHEST QUALITY WORK<br>AVAILABLE</p></div>
<div class="feature" style="left:870px"><svg width="56" height="54" viewBox="0 0 56 54"><rect x="8" y="22" width="40" height="26" rx="2" fill="#d71f26"/><rect x="12" y="28" width="32" height="3" fill="#fff"/><rect x="12" y="36" width="32" height="2" fill="#fff"/><rect x="12" y="41" width="32" height="2" fill="#fff"/><path d="M10 10h30l6-6 4 4-6 6v2H10z" fill="#d71f26"/></svg><p>MAINTENANCE AND<br>INSTALLING HVAC SYSTEMS</p></div>

<h2 class="head section-title" style="top:2298px;color:#222;font-size:44px">Our Products</h2>
<div class="product" style="left:9px;background:var(--navy)"><div class="frame photo" role="img" aria-label="Air conditioner vent grille part" style="position:absolute;background:radial-gradient(circle at 50% 50%,#8a8d93 0%,#c9cbcf 30%,#fff 55%)"></div><h3>Lorem ipsum dolor</h3></div>
<div class="product" style="left:409px;background:var(--red)"><div class="frame photo" role="img" aria-label="Heat exchanger coil component" style="position:absolute;background:radial-gradient(circle at 50% 50%,#a8aaad 0%,#d9dadc 30%,#fff 55%)"></div><h3>Lorem ipsum dolor</h3></div>
<div class="product" style="left:808px;background:var(--navy)"><div class="frame photo" role="img" aria-label="HVAC air filter panel" style="position:absolute;background:radial-gradient(circle at 50% 50%,#5a5c60 0%,#bfc1c4 30%,#fff 55%)"></div><h3>Lorem ipsum dolor</h3></div>
<span class="round" style="left:562px;top:2904px;width:34px;height:34px;background:#fff;box-shadow:0 2px 6px rgba(0,0,0,.15)"><svg width="12" height="12" viewBox="0 0 12 12"><path d="M8 1 3 6l5 5" fill="none" stroke="#222" stroke-width="1.6"/></svg></span>
<span class="round" style="left:604px;top:2904px;width:34px;height:34px;background:#fff;box-shadow:0 2px 6px rgba(0,0,0,.15)"><svg width="12" height="12" viewBox="0 0 12 12"><path d="m4 1 5 5-5 5" fill="none" stroke="#222" stroke-width="1.6"/></svg></span>

<section class="abs portfolio"></section>
<h2 class="head section-title" style="top:3066px;color:#fff;font-size:44px">Portfolio</h2>
<div class="photo" role="img" aria-label="Technicians servicing an outdoor condenser unit" style="left:114px;top:3146px;width:471px;height:244px;background:linear-gradient(135deg,#4b5a86,#2f3d6e 50%,#5e6b92)"></div>
<span class="round" style="left:315px;top:3235px;width:66px;height:66px;background:#fff"><svg width="18" height="18" viewBox="0 0 18 18"><path d="M9 2v14M2 9h14" stroke="#1f2d6b" stroke-width="2.6"/></svg></span>
<div class="photo" role="img" aria-label="Technician in hard hat wiring an HVAC unit" style="left:610px;top:3146px;width:223px;height:244px;background:linear-gradient(135deg,#c7c3b8,#3e3a36 55%,#c9a23a)"></div>
<div class="photo" role="img" aria-label="Technician drilling to mount an indoor unit" style="left:859px;top:3146px;width:222px;height:244px;background:linear-gradient(135deg,#e9e9ea,#b9c4d8 55%,#2f5fb0)"></div>
<div class="photo" role="img" aria-label="Technician fixing a wall air conditioner" style="left:114px;top:3413px;width:221px;height:242px;background:linear-gradient(135deg,#f0f0f0,#c6c6c6 55%,#3a3a3a)"></div>
<div class="photo" role="img" aria-label="Technician servicing an outdoor fan unit" style="left:362px;top:3413px;width:223px;height:242px;background:linear-gradient(135deg,#8a5a3a,#b9b6b2 55%,#e8e8e8)"></div>
<div class="photo" role="img" aria-label="Technician installing a ceiling cassette air conditioner in an office" style="left:610px;top:3413px;width:471px;height:242px;background:linear-gradient(135deg,#f2f2f2,#d7dadd 55%,#7a93b9)"></div>

<h2 class="head section-title" style="top:3873px;color:#222;font-size:44px">Get in Touch</h2>
<div class="field" style="left:184px;top:3966px;width:405px;height:59px">Name</div>
<div class="field" style="left:184px;top:4043px;width:405px;height:59px">Company name</div>
<div class="field" style="left:184px;top:4121px;width:405px;height:59px">Email</div>
<div class="field" style="left:184px;top:4199px;width:405px;height:59px">Phone</div>
<div class="field" style="left:611px;top:3966px;width:406px;height:210px;align-items:flex-start;padding-top:22px">Text here...</div>
<a class="abs" style="left:611px;top:4199px;width:406px;height:57px;background:var(--red);border-radius:3px;color:#fff;font-size:13px;font-weight:500;display:flex;align-items:center;justify-content:center">SEND NOW</a>

<svg class="abs footer" width="1200" height="496" viewBox="0 0 1200 496"><polygon points="0,86 600,0 1200,86 1200,496 0,496" fill="#d71f26"/><polygon points="0,92 600,10 1200,92 1200,496 0,496" fill="#1f2d6b"/></svg>
<div class="brand" style="left:151px;top:4530px;width:240px;color:#fff;font-size:17px"><span class="dot"></span><span>Coastal Breeze<br>Cooling Company</span></div>
<p class="abs" style="left:151px;top:4612px;width:228px;font-size:13px;line-height:21px;color:#fff;text-align:justify">Lorem ipsum dolor sit amet, consectetur adipiscing elit, sed do eiusmod tempor incididunt ut labore et dolore magna aliqua.</p>
<h4 class="foot-h" style="left:460px">Quick Links</h4>
<ul class="foot-list" style="left:461px"><li>Home</li><li>About</li><li>Services</li><li>Project</li><li>News</li><li>Contact</li></ul>
<h4 class="foot-h" style="left:640px">Support</h4>
<ul class="foot-list" style="left:641px"><li>Privacy policy</li><li>Terms of Service</li><li>Faq</li><li>Contact</li><li>Blog</li><li>Support</li></ul>
<h4 class="foot-h" style="left:833px">Contact Us</h4>
<div class="contact-item" style="top:4577px"><span class="ic"><svg width="12" height="14" viewBox="0 0 12 16"><path d="M6 0a6 6 0 0 0-6 6c0 4.5 6 10 6 10s6-5.5 6-10a6 6 0 0 0-6-6zm0 8.5A2.5 2.5 0 1 1 6 3.5a2.5 2.5 0 0 1 0 5z" fill="#d71f26"/></svg></span>123, Lorem ipsum dolor sit amet</div>
<div class="contact-item" style="top:4621px"><span class="ic"><svg width="14" height="11" viewBox="0 0 14 11"><rect width="14" height="11" rx="1" fill="#d71f26"/><path d="M1 1l6 5 6-5" fill="none" stroke="#fff" stroke-width="1.3"/></svg></span>hello@coastalbreezecooling.com</div>
<div class="contact-item" style="top:4663px"><span class="ic"><svg width="13" height="13" viewBox="0 0 24 24"><path fill="#d71f26" d="M6.6 10.8a15 15 0 0 0 6.6 6.6l2.2-2.2c.3-.3.7-.4 1-.2 1.1.4 2.3.6 3.6.6.6 0 1 .4 1 1V20c0 .6-.4 1-1 1A17 17 0 0 1 3 4c0-.6.4-1 1-1h3.5c.6 0 1 .4 1 1 0 1.3.2 2.5.6 3.6.1.3 0 .7-.2 1z"/></svg></span>+1 555 014 2030</div>

<div class="bottom-bar"></div>
<p class="abs" style="left:0;top:4772px;width:1200px;text-align:center;font-size:14px;color:#fff">© Copyrights 2024 Coastal Breeze Cooling Company | All Rights Reserved | Privacy Policy</p>
<span class="social" style="left:540px"></span>
<span class="social" style="left:583px"></span>
<span class="social" style="left:627px"></span>

</body>
</html>
```